MOVIE POSTER - THRILLER/SUSPENSE - FEATURE FILM

We need a "coming soon" poster. We prefer that the final file is delivered as a photoshop file or similar so we can edit cast/crew/etc. once that information is available. For now, it can just say COMING SOON.

TITLE OF THE MOVIE: Quiet Roads Of Marrow
TAGLINE: Seeing the future can't save you.
We are open to creative ideas on a cool font.
STORYLINE: QUIET ROADS OF MARROW is a suspenseful story laced with mystery. A woman named Wren witnesses a crime and flees the scene, wrecking her car as she escapes. Days later at the hospital, Wren awakens from a coma but has no recollection of the events that put her there. However, she is having some very strange aftereffects.... when the doctors brought her back from the brink of death, she brought back a little something extra: She's having visions of her future kidnapping and murder! It's a race against the clock as Wren tries to figure out who she can trust and who is trying to kill her. The most important question of all is: Can she solve her own murder before it happens and save herself?

SIZE: 30" x 40" - 300dpi

Elements you can include (but are not required):
Handgun
blonde female (long hair), but don't show the face
darker hair male, but don't show the face
1970 Ravenna (not a main component, but could be background) (black)
missing person flier

MOOD IDEAS:
mystery
thriller
suspense
bad guys/local thugs/mafia type/not dressed well though/more street type

I like the finish style which gives posters a slight unpolished look to it (so it's more like a drawing almost, and not a glossy photograph). Here are a couple examples of the finish that I am talking about:
http://www.reelplakat.com/2015/broken_ridge_ver4.html
http://www.reelplakat.com/2015/cobalt_quartet_ver5.html

Here was a rough mock-up I put together but by no means what we want. It was just to create a mood and feel.
http://glimmerbark.com/images/PosterQuietRoads.jpg

Here are a few posters that we like:
http://www.reelplakat.com/2010/hollow_creek.html
http://www.reelplakat.com/2001/coral_tide_ver6.html
http://www.reelplakat.com/2001/iron_keep_ver1.html
http://www.reelplakat.com/2004/mesquite_ver2.html
http://www.reelplakat.com/2008/ride_past_the_grey_edge.html
These are just a few ideas, but we are open to original ideas.

Please feel free to ask questions! We look forward to working with you.

Industry/Entity Type

Movie

Requirements
Must have
• Information and examples are in the "project description."
Nice to have
Should not have

```html
<!DOCTYPE html>
<html lang="en">
<head>
<meta charset="utf-8">
<title>Quiet Roads Of Marrow – Coming Soon Poster</title>
<link rel="stylesheet" href="https://fonts.googleapis.com/css2?family=Josefin+Sans:wght@300;400;600&display=swap">
<style>
  :root {
    --backdrop: #e9e7e4;
    --poster-red: #e00006;
    --poster-red-deep: #c80005;
    --ink: #141010;
    --paper-white: #ffffff;
    --figure-dark: #2a2a2a;
    --figure-mid: #6b6b6b;
  }
  * { margin: 0; padding: 0; box-sizing: border-box; }
  html, body {
    width: 1200px;
    height: 1148px;
    overflow: hidden;
    background: var(--backdrop);
  }
  .poster {
    position: absolute;
    left: 187px;
    top: 24px;
    width: 825px;
    height: 1100px;
    background: linear-gradient(160deg, var(--poster-red) 0%, var(--poster-red) 60%, var(--poster-red-deep) 100%);
    overflow: hidden;
    font-family: "Josefin Sans", "Futura", sans-serif;
    color: var(--ink);
  }
  .coming-soon {
    position: absolute;
    top: 52px;
    left: 60px;
    right: 60px;
    text-align: center;
    color: var(--paper-white);
    font-weight: 300;
    font-size: 15px;
    letter-spacing: 22px;
  }
  .lead-figure {
    position: absolute;
    left: 580px;
    top: 270px;
    width: 136px;
    height: 530px;
  }
  .tagline {
    position: absolute;
    left: 172px;
    top: 590px;
    font-size: 17px;
    font-weight: 400;
    letter-spacing: 0.5px;
  }
  .title {
    position: absolute;
    left: 110px;
    top: 614px;
    width: 680px;
    text-transform: uppercase;
    font-weight: 400;
  }
  .title-line {
    display: flex;
    align-items: baseline;
    white-space: nowrap;
  }
  .title-line-second { margin-left: 176px; margin-top: -6px; }
  .title-small { font-weight: 300; font-size: 34px; line-height: 1; }
  .title-large { font-weight: 600; font-size: 112px; line-height: 0.95; letter-spacing: -3px; }
  .word-roads { margin: 0 10px 0 4px; }
  .soft { filter: blur(3px); opacity: 0.92; }
</style>
</head>
<body>
  <main class="poster">
    <p class="coming-soon">COMING SOON...</p>

    <svg class="lead-figure" viewBox="0 0 136 530" role="img" aria-label="Black-and-white photo of a blonde woman seen from behind in a black jacket and jeans, holding a handgun at her side">
      <defs>
        <linearGradient id="figure-tone" x1="0" y1="0" x2="0" y2="1">
          <stop offset="0" stop-color="#bdbdbd"/>
          <stop offset="0.15" stop-color="var(--figure-dark)"/>
          <stop offset="0.45" stop-color="var(--figure-dark)"/>
          <stop offset="0.55" stop-color="var(--figure-mid)"/>
          <stop offset="1" stop-color="#3a3a3a"/>
        </linearGradient>
      </defs>
      <rect x="0" y="0" width="136" height="530" rx="40" fill="url(#figure-tone)" opacity="0.85"/>
    </svg>

    <p class="tagline">SEEING THE FUTURE CAN'T SAVE YOU.</p>

    <h1 class="title" aria-label="Quiet Roads Of Marrow">
      <span class="title-line">
        <span class="title-small">Quiet</span>
        <span class="title-large word-roads">Roads</span>
        <span class="title-small">Of</span>
      </span>
      <span class="title-line title-line-second">
        <span class="title-large">Mar<span class="soft">row</span></span>
      </span>
    </h1>
  </main>
</body>
</html>
```